Psychiatric Office Needs a Website- 1st Time Ever!

Been in practice since 2003 with no website, but finally ready to dive in. We are Maplecrest Behavioral Healthcare, a mental health outpatient practice based in Fayetteville, Georgia that sees diverse individuals and families from childhood to advanced age for a variety of conditions. We've grown by word of mouth and referral but would now like to have a digital footprint. Be the pioneer of our website and we will be sure to share. We would like to see designs that are modern, animated, fairly colorful, easy to read, and caters to all ages. Also, we would like the design to take the whole page (not be centered) and can be viewed well on phone/tablet. Please see our outline for more information. Our motto/slogan is: Maplecrest Behavioral Healthcare- A step forward in your wellness journey, so the design should try to reflect that.
Updates

Project Deadline Extended
Reason: site in progress

Target Market(s)

Children through elderly

Industry/Entity Type

Medical

Logo Text

Stepping forward in your wellness journey

Number of Pages Required

1 page

Colors

Designer to choose colors to be used in the design.

Requirements
Must have
• Animation or moving pictures.
• Color.
• Concise.
• User friendly
• Diversity in the stock photos

```html
<!DOCTYPE html>
<html lang="en">
<head>
<meta charset="utf-8">
<title>Maplecrest Behavioral Healthcare</title>
<link rel="stylesheet" href="https://fonts.googleapis.com/css2?family=Asap:wght@400;500;700&family=Arimo:wght@400;700&display=swap">
<style>
:root{
  --purple:#7a64a6;
  --purple-light:#9a86c2;
  --purple-dark:#5e4b88;
  --purple-soft:#b9a9d8;
  --ink:#3c3c3c;
  --muted:#6b6b6b;
  --white:#ffffff;
  --line:#d9d3e6;
  --footer:#2d2623;
}
*{box-sizing:border-box;margin:0;padding:0}
html,body{width:1200px;height:3455px;overflow:hidden}
body{font-family:"Arimo",Arial,sans-serif;color:var(--ink);background:var(--white);position:relative}
.abs{position:absolute}
.heading{font-family:"Asap",Arial,sans-serif;font-weight:400}

/* top bar + header */
.topbar{left:0;top:0;width:1200px;height:39px;background:#fff;font-family:"Asap",sans-serif;font-size:13px;color:#333;z-index:2}
.topbar span{position:absolute;top:12px;display:flex;align-items:center;gap:8px}
.site-header{left:0;top:39px;width:1200px;height:81px;background:#fff}
.brand{left:80px;top:10px;width:106px;height:106px;border-radius:50%;background:var(--purple);border:4px solid #fff;box-shadow:0 0 0 2px var(--purple-soft);display:flex;align-items:center;justify-content:center;text-align:center;color:#fff;font-family:"Asap",sans-serif;font-size:12px;line-height:1.25;padding:10px;z-index:3}
.nav{left:357px;top:0;height:81px;display:flex;font-family:"Asap",sans-serif;font-size:16px;color:#555}
.nav a{display:block;padding:32px 21px 0;text-decoration:none;color:#555}
.nav a.active{background:var(--purple);color:#fff;padding:32px 31px 0}

/* hero */
.hero{left:0;top:120px;width:1200px;height:571px;background:linear-gradient(100deg,#b9876a 0%,#e7c2a2 30%,#f4dcc2 50%,#c89a7b 75%,#8c6a55 100%)}
.hero-box{left:212px;top:161px;width:778px;height:120px;background:rgba(60,45,40,.42);text-align:center;color:#fff}
.hero-title{font-size:50px;margin-top:16px;letter-spacing:.5px;line-height:58px}
.hero-tag{font-family:"Asap",sans-serif;font-style:italic;font-size:20px;margin-top:0;line-height:26px}
.btn-contact{left:296px;top:125px;width:184px;height:55px;background:var(--purple);color:#fff;font-family:"Asap",sans-serif;font-size:20px;line-height:55px}

/* vision / mission */
.vm{left:0;top:691px;width:1200px;height:368px}
.vm-left{left:0;top:0;width:599px;height:368px;background:var(--purple)}
.vm-title{font-size:36px;display:flex;align-items:center;gap:14px}
.vm-text{font-size:14px;line-height:25.5px;width:350px}
.seal{left:455px;top:37px;width:290px;height:290px;border-radius:50%;background:var(--purple);border:8px solid #fff;box-shadow:0 0 0 3px var(--purple-soft);color:#fff;display:flex;align-items:center;justify-content:center;text-align:center;font-family:"Asap",sans-serif;font-size:26px;line-height:1.3;padding:30px}

/* services */
.services{left:0;top:1059px;width:1200px;height:834px;background:radial-gradient(ellipse at 50% 40%,#4a4440 0%,#302c2a 60%,#221f1e 100%)}
.sec-title{font-size:36px;color:#fff;text-align:center;width:100%;top:50px}
.sec-title span{display:inline-block;border-bottom:2px solid #fff;padding:0 6px 4px}
.svc{font-size:14px;line-height:20px;color:#fff;width:250px}
.svc h3{font-family:"Asap",sans-serif;font-weight:400;font-size:16px;color:var(--purple-soft);margin-bottom:2px}
.svc a{color:#fff;font-weight:700;text-decoration:underline}

/* conditions */
.conditions{left:0;top:1893px;width:1200px;height:548px;background:linear-gradient(90deg,#6f5a9b,#8e7ab9)}
.card{width:249px;color:#fff;text-align:center}
.card-img{width:249px;height:168px;border:3px solid #fff;box-shadow:0 4px 8px rgba(0,0,0,.35)}
.card h4{font-family:"Asap",sans-serif;font-weight:400;font-size:20px;margin-top:22px;line-height:22px;height:44px}
.card p{font-size:13px;line-height:19px;margin-top:2px}
.arrow{width:30px;height:30px;background:#fff;color:var(--purple);font-size:18px;text-align:center;line-height:28px}
.dots{left:572px;display:flex;gap:4px}
.dots i{display:block;width:13px;height:13px;border:2px solid #fff}
.dots i.on{background:#fff}

/* faq + news */
.faq-title,.news-title{font-size:36px;color:var(--purple)}
.faq-item{left:81px;width:518px;border:1px solid var(--line);font-family:"Asap",sans-serif;font-size:19px;color:var(--purple);padding:8px 12px;display:flex;align-items:center;gap:14px;background:#fff}
.faq-item b{font-size:26px;color:var(--purple);font-weight:700;width:18px;text-align:center;line-height:20px}
.faq-body{font-size:12px;line-height:18px;color:#555;padding:10px 14px;border-top:1px solid var(--line)}
.divider{left:613px;top:2455px;width:4px;height:410px;background:#eee}
.news-img{width:115px;height:115px}
.news h5{font-family:"Asap",sans-serif;font-weight:400;font-size:18px;color:var(--purple)}
.news .date{font-size:11px;color:#777;margin:6px 0 4px}
.news p{font-size:13px;line-height:19px;color:#555}
.news .more{font-size:12px;color:var(--purple);margin-top:8px;letter-spacing:.5px}

/* cta */
.cta{left:0;top:2874px;width:1200px;height:104px;background:var(--purple)}
.cta p{left:81px;top:28px;width:780px;font-size:15px;line-height:24px;color:#fff}
.btn-form{left:893px;top:23px;width:231px;height:58px;background:#fff;border:2px solid var(--purple-soft);color:var(--purple);font-family:"Asap",sans-serif;font-size:20px;text-align:center;line-height:54px}

/* footer */
.footer{left:0;top:2978px;width:1200px;height:398px;background:linear-gradient(100deg,#3a2f2a,#2a2320 50%,#3b302b)}
.f-title{font-family:"Asap",sans-serif;font-weight:400;font-size:21px;color:#fff;letter-spacing:.5px}
.field{left:81px;width:444px;height:42px;background:#fff;font-size:13px;color:#777;padding:12px 12px}
.submit{left:81px;top:344px;width:184px;height:52px;background:var(--purple);color:#fff;font-family:"Asap",sans-serif;font-size:19px;text-align:center;line-height:52px}
.f-links{list-style:none;font-size:14px;color:#fff;line-height:29px}
.f-links li::before{content:"";display:inline-block;width:7px;height:7px;border-radius:50%;background:#c9c3d6;margin-right:10px;vertical-align:middle}
.find{font-size:14px;color:#fff;line-height:24px}
.find-row{display:flex;gap:18px;align-items:flex-start}
.social{display:flex;gap:14px}
.social i{display:block;width:46px;height:46px;border-radius:50%;background:var(--purple);border:2px solid var(--purple-soft)}
.copy{left:0;top:3376px;width:1200px;height:79px;background:#2a2422;border-top:1px solid #555;color:#fff;font-size:14px;text-align:center;line-height:79px}
.copy b{font-weight:700}
</style>
</head>
<body>

<div class="abs topbar">
  <span style="left:506px">
    <svg width="16" height="16" viewBox="0 0 16 16"><circle cx="8" cy="8" r="6.5" fill="none" stroke="#444" stroke-width="1.5"/><path d="M8 4v4l3 2" fill="none" stroke="#444" stroke-width="1.5"/></svg>
    Monday - Friday : 10.00 A.M to 8.00 P.M</span>
  <span style="left:815px">
    <svg width="18" height="18" viewBox="0 0 18 18"><circle cx="9" cy="9" r="8" fill="none" stroke="#444" stroke-width="1.3"/><path d="M6 5c0 4 3 7 7 7l-1.5-2-2 .5-2.5-2.5.5-2z" fill="#444"/></svg>
    +1-555-014-2893</span>
  <span style="left:980px">LOGIN
    <svg width="14" height="16" viewBox="0 0 14 16"><circle cx="7" cy="4.5" r="3.5" fill="#444"/><path d="M0 16c0-5 3-7 7-7s7 2 7 7z" fill="#444"/></svg>
    Patient</span>
</div>

<header class="abs site-header">
  <nav class="abs nav">
    <a class="active">Home</a><a>About Us</a><a>Services</a><a>Conditions We Treat</a><a>New Patients</a><a>Contact Us</a>
  </nav>
</header>
<div class="abs brand">Maplecrest Behavioral Healthcare</div>

<section class="abs hero" role="img" aria-label="Photo of a diverse group of smiling young friends outdoors">
  <div class="abs hero-box">
    <h1 class="heading hero-title">Maplecrest Behavioral Healthcare</h1>
    <p class="hero-tag">A step forward in your wellness journey</p>
    <div class="abs btn-contact">CONTACT US</div>
  </div>
</section>

<section class="abs vm">
  <div class="abs vm-left"></div>
  <div class="abs" style="left:81px;top:60px;color:#fff">
    <h2 class="heading vm-title">
      <svg width="32" height="36" viewBox="0 0 32 36"><path d="M4 18l18-12 4 6-18 12z" fill="#fff"/><path d="M14 20l-8 14M14 20l8 14M14 20v14" stroke="#fff" stroke-width="2.5"/></svg>
      VISION</h2>
    <div style="position:absolute;left:44px;top:52px;width:190px;height:2px;background:#fff"></div>
    <p class="vm-text" style="margin-top:22px">Lorem Ipsum is simply dummy text of the printing and typesetting industry. Lorem Ipsum has been the industry's standard dummy text ever since the 1500s, when an unknown printer took a galley of type and scrambled it to make a type specimen book. It has survived not only five centuries, but also the leap into electronic typesetting, remaining essentially unchanged.</p>
  </div>
  <div class="abs" style="left:771px;top:60px;color:var(--purple)">
    <h2 class="heading vm-title">
      <svg width="36" height="36" viewBox="0 0 36 36"><circle cx="16" cy="20" r="13" fill="none" stroke="#7a64a6" stroke-width="3"/><circle cx="16" cy="20" r="6" fill="none" stroke="#7a64a6" stroke-width="3"/><path d="M16 20L32 4M26 4h6v6" fill="none" stroke="#7a64a6" stroke-width="3"/></svg>
      MISSION</h2>
    <div style="position:absolute;left:50px;top:52px;width:190px;height:2px;background:var(--purple)"></div>
    <p class="vm-text" style="margin-top:22px;color:#555">Lorem Ipsum is simply dummy text of the printing and typesetting industry. Lorem Ipsum has been the industry's standard dummy text ever since the 1500s, when an unknown printer took a galley of type and scrambled it to make a type specimen book. It has survived not only five centuries, but also the leap into electronic typesetting, remaining essentially unchanged.</p>
  </div>
  <div class="abs seal">Maplecrest Behavioral Healthcare</div>
</section>

<section class="abs services">
  <h2 class="abs heading sec-title"><span>SERVICES</span></h2>
  <svg class="abs" style="left:0;top:0" width="1200" height="834" viewBox="0 0 1200 834" role="img" aria-label="Round photos of clinicians with patients of all ages around a central hub">
    <g stroke="#d8d2e4" stroke-width="3">
      <line x1="599" y1="383" x2="490" y2="203"/>
      <line x1="599" y1="383" x2="686" y2="189"/>
      <line x1="599" y1="383" x2="389" y2="355"/>
      <line x1="599" y1="383" x2="797" y2="339"/>
      <line x1="599" y1="383" x2="444" y2="530"/>
      <line x1="599" y1="383" x2="765" y2="518"/>
      <line x1="599" y1="383" x2="606" y2="601"/>
    </g>
    <g fill="#fff">
      <circle cx="540" cy="286" r="6"/><circle cx="645" cy="284" r="6"/><circle cx="496" cy="369" r="6"/>
      <circle cx="700" cy="361" r="6"/><circle cx="525" cy="454" r="6"/><circle cx="677" cy="454" r="6"/><circle cx="603" cy="487" r="6"/>
    </g>
    <circle cx="599" cy="383" r="103" fill="#e9e6ef" stroke="#fff" stroke-width="4"/>
    <g stroke="#fff" stroke-width="5">
      <circle cx="490" cy="203" r="64" fill="#8d7ab3"/><circle cx="490" cy="203" r="56" fill="#d7c4b3" stroke="none"/>
      <circle cx="686" cy="189" r="64" fill="#8d7ab3"/><circle cx="686" cy="189" r="56" fill="#cbb39d" stroke="none"/>
      <circle cx="389" cy="355" r="64" fill="#8d7ab3"/><circle cx="389" cy="355" r="56" fill="#c9b7a8" stroke="none"/>
      <circle cx="797" cy="339" r="64" fill="#8d7ab3"/><circle cx="797" cy="339" r="56" fill="#d3bfa6" stroke="none"/>
      <circle cx="444" cy="530" r="64" fill="#8d7ab3"/><circle cx="444" cy="530" r="56" fill="#c4b6ad" stroke="none"/>
      <circle cx="765" cy="518" r="64" fill="#8d7ab3"/><circle cx="765" cy="518" r="56" fill="#d6c6b4" stroke="none"/>
      <circle cx="606" cy="601" r="64" fill="#8d7ab3"/><circle cx="606" cy="601" r="56" fill="#bfae9f" stroke="none"/>
    </g>
  </svg>
  <div class="abs svc" style="left:138px;top:156px;width:290px"><h3>Diagnostic evaluation and treatment</h3>Lorem Ipsum is simply dummy text<br>of the printing and text typesetting<br>industry.<a>READ MORE</a></div>
  <div class="abs svc" style="left:771px;top:140px"><h3>Disability and work-related reports</h3>Lorem Ipsum is simply dummy text of the printing and text typesetting industry.<a>READ MORE</a></div>
  <div class="abs svc" style="left:81px;top:326px;width:230px"><h3>Psychopharmacology</h3>Lorem Ipsum is simply dummy text of the printing and text typesetting industry.<a>READ MORE</a></div>
  <div class="abs svc" style="left:888px;top:296px"><h3>Early childhood Assessments</h3>Lorem Ipsum is simply dummy text of the printing and text typesetting industry.<a>READ MORE</a></div>
  <div class="abs svc" style="left:101px;top:514px;width:270px"><h3>Bariatric pre-surgical consultation</h3>Lorem Ipsum is simply dummy text<br>of the printing and text typesetting<br>industry.<a>READ MORE</a></div>
  <div class="abs svc" style="left:864px;top:484px"><h3>Substance abuse assessments</h3>Lorem Ipsum is simply dummy text of the printing and text typesetting industry.<a>READ MORE</a></div>
  <div class="abs svc" style="left:501px;top:690px;width:210px"><h3>Developmental disabilities</h3>Lorem Ipsum is simply dummy text of the printing and text typesetting industry.<a>READ MORE</a></div>
</section>

<section class="abs conditions">
  <h2 class="abs heading sec-title" style="top:56px"><span>CONDITIOND WE TREAT</span></h2>
  <div class="abs arrow" style="left:32px;top:213px">&#8249;</div>
  <div class="abs arrow" style="left:1140px;top:213px">&#8250;</div>
  <div class="abs card" style="left:81px;top:150px">
    <div class="card-img" role="img" aria-label="Photo of a woman holding her head in distress" style="background:linear-gradient(135deg,#3a3330,#a08a7c)"></div>
    <h4>Mood Disorders</h4>
    <p>Lorem Ipsum is simply dummy text of the printing and typesetting industry. Lorem Ipsum has been the industry's standard dummy text ever since.</p>
  </div>
  <div class="abs card" style="left:345px;top:150px">
    <div class="card-img" role="img" aria-label="Photo of a counselor comforting a patient" style="background:linear-gradient(135deg,#c9b7a5,#5f78a8)"></div>
    <h4>Anxiety Disorders</h4>
    <p>Lorem Ipsum is simply dummy text of the printing and typesetting industry. Lorem Ipsum has been the industry's standard dummy text ever since.</p>
  </div>
  <div class="abs card" style="left:610px;top:150px">
    <div class="card-img" role="img" aria-label="Photo of a therapy session with an older man" style="background:linear-gradient(135deg,#e0d9d2,#8a7260)"></div>
    <h4>Psychotic Disorders</h4>
    <p>Lorem Ipsum is simply dummy text of the printing and typesetting industry. Lorem Ipsum has been the industry's standard dummy text ever since.</p>
  </div>
  <div class="abs card" style="left:875px;top:150px">
    <div class="card-img" role="img" aria-label="Photo of a mother hugging her young daughter" style="background:linear-gradient(135deg,#7a4f3a,#d4a47e)"></div>
    <h4>Common Disorders<br>of Childhood</h4>
    <p>Lorem Ipsum is simply dummy text of the printing and typesetting industry. Lorem Ipsum has been the industry's standard dummy text ever since.</p>
  </div>
  <div class="abs dots" style="top:516px"><i></i><i class="on"></i><i></i></div>
</section>

<section>
  <h2 class="abs heading faq-title" style="left:81px;top:2494px">FAQ</h2>
  <div class="abs" style="left:81px;top:2552px;width:518px;border:1px solid var(--line)">
    <div class="faq-item" style="position:static;border:0"><b>&minus;</b>What do I need to bring with me to my first visit?</div>
    <p class="faq-body">Lorem Ipsum is simply dummy text of the printing and typesetting industry. Lorem Ipsum has been the industry's standard dummy text ever since the 1500s,It has survived not only five centuries, but also the leap into electronic typesetting, remaining essentially unchanged.</p>
  </div>
  <div class="abs faq-item" style="top:2686px"><b>+</b>How long do I have to wait to be seen?</div>
  <div class="abs faq-item" style="top:2728px"><b>+</b>Why is my child not doing well in school?</div>
  <div class="abs faq-item" style="top:2770px"><b>+</b>What typs of insurance do you accept?</div>
</section>
<div class="abs divider"></div>

<section>
  <h2 class="abs heading news-title" style="left:668px;top:2494px">LATEST NEWS</h2>
  <div class="abs news-img" role="img" aria-label="Photo of a thoughtful young woman" style="left:668px;top:2549px;background:linear-gradient(135deg,#4f6f9a,#c8a28a)"></div>
  <div class="abs news" style="left:799px;top:2550px;width:330px">
    <h5>Lorem Ipsum is simply dummy text</h5>
    <p class="date">&#128197; 10 JULY 2016</p>
    <p>Lorem Ipsum is simply dummy text of the printing and typesetting industry......</p>
    <p class="more">READ MORE &nbsp;&nbsp;&raquo;</p>
  </div>
  <div class="abs" style="left:799px;top:2692px;width:280px;height:1px;background:var(--line)"></div>
  <div class="abs news-img" role="img" aria-label="Photo of a family reading together" style="left:668px;top:2713px;background:linear-gradient(135deg,#d9c4ae,#7b5a45)"></div>
  <div class="abs news" style="left:799px;top:2710px;width:330px">
    <h5>Lorem Ipsum is simply dummy text</h5>
    <p class="date">&#128197; 10 JULY 2016</p>
    <p>Lorem Ipsum is simply dummy text of the printing and typesetting industry......</p>
    <p class="more">READ MORE &nbsp;&nbsp;&raquo;</p>
  </div>
</section>

<section class="abs cta">
  <p class="abs">Lorem Ipsum is simply dummy text of the printing and typesetting industry. Lorem Ipsum has been the industry's standard dummy text ever since the 1500s, when an unknown printer took a galley of type and scrambled.</p>
  <div class="abs btn-form">NEW PATIENT FORM</div>
</section>

<footer class="abs footer" role="img" aria-label="Dimmed background photo of smiling people">
  <h3 class="abs f-title" style="left:81px;top:57px">QUICK INQUIRY</h3>
  <div class="abs field" style="top:104px">Name*</div>
  <div class="abs field" style="top:152px">Email*</div>
  <div class="abs field" style="top:200px">Services*</div>
  <div class="abs field" style="top:248px;height:88px">Message*</div>
  <div class="abs submit">SUBMIT</div>

  <h3 class="abs f-title" style="left:569px;top:57px">OUR SERVICES</h3>
  <ul class="abs f-links" style="left:592px;top:98px">
    <li>Home</li><li>About Us</li><li>Services</li><li>Conditions We Treat</li><li>New Patients</li><li>Contact Us</li>
  </ul>

  <h3 class="abs f-title" style="left:871px;top:57px">FIND US</h3>
  <div class="abs find" style="left:871px;top:102px;width:300px">
    <div class="find-row"><svg width="18" height="24" viewBox="0 0 18 24"><path d="M9 0a8 8 0 0 0-8 8c0 6 8 16 8 16s8-10 8-16a8 8 0 0 0-8-8z" fill="#c9c3d6"/><circle cx="9" cy="8" r="3" fill="#2a2320"/></svg>
      <div>Maplecrest Behavioral Healthcare<br>Lorem Ipsum is simply dummy<br>text printing and typesetting</div></div>
    <div class="find-row" style="margin-top:14px"><svg width="22" height="20" viewBox="0 0 22 20"><path d="M3 2h5l2 5-3 2c1 3 3 5 6 6l2-3 5 2v4c-9 1-18-8-17-16z" fill="#c9c3d6"/></svg>+1-555-014-2893</div>
    <div class="find-row" style="margin-top:14px"><svg width="22" height="20" viewBox="0 0 22 20"><rect x="4" y="2" width="14" height="16" rx="2" fill="#c9c3d6"/><rect x="7" y="5" width="8" height="5" fill="#2a2320"/></svg>+1-555-014-2893</div>
    <div class="find-row" style="margin-top:14px"><svg width="22" height="18" viewBox="0 0 22 18"><rect x="1" y="2" width="20" height="14" fill="#c9c3d6"/><path d="M1 2l10 8 10-8" fill="none" stroke="#2a2320" stroke-width="1.5"/></svg>hello@maplecrestcare.example</div>
    <div class="social" style="margin-top:22px"><i></i><i></i><i></i></div>
  </div>
</footer>
<div class="abs copy">&copy; <b>MAPLECREST BEHAVIORAL HEALTHCARE</b>- 2017. All Rights Reserved</div>

</body>
</html>
```